Business Card Design for The Lending Nest Inc.

We need a business card design for our mortgage company: "The Lending Nest Inc."

Need to have Social Media Account on there as a possibility

```html
<!DOCTYPE html>
<html lang="en">
<head>
<meta charset="utf-8">
<title>The Lending Nest Inc. – Business Card</title>
<link rel="stylesheet" href="https://fonts.googleapis.com/css2?family=Lato:wght@400&family=Source+Sans+3:wght@400;600&display=swap">
<style>
  :root {
    --page-bg: #e4e4e4;
    --card-bg: #f7f7f7;
    --brand-blue: #1a56a0;
    --band-pink: #ff0a8c;
    --band-violet: #a40cf2;
    --band-indigo: #5a2cff;
    --band-blue: #1f8cf5;
    --band-aqua: #00f0c8;
    --social-a: #3b5998;
    --social-b: #1da1f2;
    --phone: #e70fae;
    --phone-text: #b8169a;
    --mail: #f4098a;
    --mail-text: #c2157a;
    --web: #1ba3d8;
    --web-text: #13879f;
    --home: #1de9c4;
    --home-text: #1aa68d;
    --link-blue: #1a4f9c;
  }
  * { margin: 0; padding: 0; box-sizing: border-box; }
  html, body { width: 1200px; height: 1200px; overflow: hidden; }
  body { background: var(--page-bg); position: relative; font-family: "Lato", sans-serif; }

  .card {
    position: absolute;
    left: 202px;
    width: 796px;
    height: 478px;
    background: linear-gradient(160deg, #ffffff 0%, var(--card-bg) 60%, #efefef 100%);
    box-shadow: 0 4px 14px rgba(0,0,0,0.18);
    overflow: hidden;
  }
  .card--front { top: 68px; }
  .card--back { top: 685px; }

  .color-band {
    position: absolute; left: 0; top: 0; width: 100%;
    background: linear-gradient(90deg, var(--band-pink) 0%, #d30bc4 18%, var(--band-violet) 32%, var(--band-indigo) 50%, var(--band-blue) 70%, #05c0ea 85%, var(--band-aqua) 100%);
  }
  .card--front .color-band { height: 157px; }
  .card--back .color-band { height: 73px; }

  .profile-photo {
    position: absolute; left: 344px; top: 22px;
    width: 110px; height: 110px; border-radius: 50%;
    background: rgba(40, 30, 140, 0.45);
  }

  .company-name {
    position: absolute; left: 0; right: 0; top: 172px;
    text-align: center;
    font-family: "Source Sans 3", sans-serif;
    font-weight: 400; font-size: 64px; line-height: 80px;
    color: var(--brand-blue);
  }

  .contact {
    position: absolute; display: flex; align-items: center;
    height: 50px;
  }
  .contact svg { flex: none; width: 50px; height: 50px; }
  .contact span { margin-left: 16px; white-space: nowrap; }

  .contact--social-a { left: 43px; top: 265px; font-size: 30px; color: var(--link-blue); }
  .contact--phone { left: 43px; top: 331px; font-size: 24px; color: var(--phone-text); }
  .contact--mail { left: 43px; top: 396px; font-size: 23px; color: var(--mail-text); }
  .contact--social-b { left: 439px; top: 273px; font-size: 30px; color: var(--social-b); }
  .contact--web { left: 436px; top: 331px; font-size: 23px; color: var(--web-text); }
  .contact--home { left: 436px; top: 396px; font-size: 23px; color: var(--home-text); }
  .contact--web span, .contact--home span { margin-left: 20px; }

  .brand-lockup {
    position: absolute; left: 0; right: 0; top: 218px;
    display: flex; align-items: center; justify-content: center; gap: 18px;
  }
  .brand-lockup .brand-dot {
    width: 60px; height: 60px; border-radius: 50%;
    background: var(--brand-blue);
  }
  .brand-lockup .brand-name {
    font-family: "Source Sans 3", sans-serif;
    font-weight: 600; font-size: 46px; color: var(--brand-blue);
  }
</style>
</head>
<body>

  <section class="card card--front">
    <div class="color-band" role="img" aria-label="Faceted polygon pattern in pink, violet, blue and aqua"></div>
    <div class="profile-photo" role="img" aria-label="Round profile photo placeholder"></div>

    <h1 class="company-name">Lending Nest Inc</h1>

    <div class="contact contact--social-a">
      <svg viewBox="0 0 50 50" aria-hidden="true"><circle cx="25" cy="25" r="25" fill="var(--social-a)"/></svg>
      <span>your page</span>
    </div>

    <div class="contact contact--phone">
      <svg viewBox="0 0 50 50" aria-hidden="true">
        <circle cx="25" cy="25" r="25" fill="var(--phone)"/>
        <path d="M17 12c2-1 4 0 5 2l2 5c1 2 0 3-1 4l-1 1c1 3 4 6 7 7l1-1c1-1 2-2 4-1l5 2c2 1 3 3 2 5l-1 2c-1 2-3 3-6 2-9-2-16-9-18-18-1-3 0-5 1-6z" fill="#fff"/>
      </svg>
      <span>1808-5550142</span>
    </div>

    <div class="contact contact--mail">
      <svg viewBox="0 0 50 50" aria-hidden="true">
        <circle cx="25" cy="25" r="25" fill="var(--mail)"/>
        <rect x="12" y="16" width="26" height="18" rx="2" fill="none" stroke="#fff" stroke-width="3"/>
        <path d="M13 18l12 9 12-9" fill="none" stroke="#fff" stroke-width="3"/>
      </svg>
      <span>office@lendingnestdemo.net</span>
    </div>

    <div class="contact contact--social-b">
      <svg viewBox="0 0 50 50" aria-hidden="true"><circle cx="25" cy="25" r="23" fill="var(--social-b)"/></svg>
      <span>your feed</span>
    </div>

    <div class="contact contact--web">
      <svg viewBox="0 0 50 50" aria-hidden="true">
        <circle cx="25" cy="25" r="25" fill="var(--web)"/>
        <g fill="none" stroke="#fff" stroke-width="2">
          <circle cx="25" cy="25" r="14"/>
          <ellipse cx="25" cy="25" rx="6" ry="14"/>
          <path d="M11 25h28M13 18h24M13 32h24M25 11v28"/>
        </g>
      </svg>
      <span>www.lendingnestdemo.net</span>
    </div>

    <div class="contact contact--home">
      <svg viewBox="0 0 50 50" aria-hidden="true">
        <circle cx="25" cy="25" r="25" fill="var(--home)"/>
        <path d="M25 12l14 13h-4v12h-7v-8h-6v8h-7V25h-4z" fill="#fff"/>
      </svg>
      <span>12th Avenue, Brookfield</span>
    </div>
  </section>

  <section class="card card--back">
    <div class="color-band" role="img" aria-label="Faceted polygon pattern in pink, violet, blue and aqua"></div>
    <div class="brand-lockup">
      <div class="brand-dot" aria-hidden="true"></div>
      <div class="brand-name">The Lending Nest Inc.</div>
    </div>
  </section>

</body>
</html>
```